larkforge website

commerce website to sell cookeries, brackets, mailboxes and to show off homes built. Modern Steel in design see marlo cycles web page to be like: https://www.marlocycles-demo.com/en/ sorry its bright nest hosting word press divi

must be able to add products to page

Target Market(s)

mainly western states of U.S.

Industry/Entity Type

Building Product

Coding

Coded - Design and coding required

Number of Pages Required

3 page

Font styles to use
Sans Serif

Colors

Designer to choose colors to be used in the design.

Requirements
Must have
• customers to be able to order products from page
• bright nest hosting word press divi

```html
<!DOCTYPE html>
<html lang="en">
<head>
<meta charset="utf-8">
<title>Larkforge — Outdoor Firepit Cookery</title>
<link href="https://fonts.googleapis.com/css2?family=Montserrat:wght@400;500;600;700&family=Roboto:wght@400;500;700&display=swap" rel="stylesheet">
<style>
:root{
  --navy:#4b5985;
  --navy-dark:#3c4870;
  --ink:#1f2230;
  --text:#333;
  --muted:#8a8d96;
  --line:#e2e3e8;
  --gray-band:#eeeff3;
  --red:#e0201b;
  --footer:#111216;
  --white:#fff;
}
*{box-sizing:border-box;margin:0;padding:0}
html,body{width:1200px;height:3812px;overflow:hidden;background:var(--white)}
body{font-family:'Roboto',sans-serif;color:var(--text)}
.page{position:relative;width:1200px;height:3812px;overflow:hidden}
.abs{position:absolute}

/* top bar */
.topbar{left:0;top:0;width:1200px;height:44px;background:var(--navy);color:#fff;font-size:13px}
.topbar span{position:absolute;top:14px;white-space:nowrap}
.topbar .sep{width:1px;height:26px;top:9px;background:rgba(255,255,255,.35)}
.navbar{left:0;top:44px;width:1200px;height:60px;background:#fff;border-bottom:1px solid var(--line)}
.navbar a{position:absolute;top:21px;font-size:14px;color:var(--ink);text-decoration:none;font-weight:500;white-space:nowrap}
.navbar a.active{color:var(--navy)}
.brand-diamond{left:497px;top:2px;width:206px;height:206px}
.brand-name{left:500px;top:112px;width:200px;text-align:center;color:#fff;font-weight:500;font-size:20px;letter-spacing:1px}

/* hero */
.hero-photo{left:0;top:104px;width:1200px;height:700px;background:linear-gradient(180deg,#6b9a36 0%,#4d8a22 45%,#3c7a18 100%)}
.hero-grill{left:600px;top:190px;width:380px;height:480px;background:radial-gradient(ellipse at 50% 35%,rgba(40,40,42,.55) 0%,rgba(50,50,50,.25) 40%,rgba(60,60,60,0) 68%)}
.hero-title{left:210px;top:290px;color:#fff;font-family:'Montserrat',sans-serif;font-weight:700;font-size:52px;line-height:60px}
.hero-sub{left:212px;top:366px;color:#fff;font-size:16px;font-weight:500}
.btn-outline-light{left:213px;top:411px;width:160px;height:49px;border:2px solid #fff;border-radius:25px;color:#fff;font-size:14px;font-weight:700;display:flex;align-items:center;justify-content:center}
.hero-arrow{width:44px;height:44px;border:2px solid rgba(255,255,255,.8);border-radius:50%;display:flex;align-items:center;justify-content:center}

.btn{display:flex;align-items:center;justify-content:center;border:2px solid var(--navy);border-radius:26px;color:var(--navy);font-weight:700;font-size:15px;background:#fff;white-space:nowrap}
.btn.filled{background:var(--navy);color:#fff}

/* welcome */
.welcome-top{left:0;top:838px;width:1200px;text-align:center;font-family:'Montserrat',sans-serif;font-size:28px;color:#111;font-weight:500}
.welcome-brand{left:0;top:874px;width:1200px;text-align:center;font-family:'Montserrat',sans-serif;font-size:40px;color:var(--navy);font-weight:500}
.welcome-brand b{font-weight:700}
.welcome-text{left:160px;top:938px;width:880px;text-align:center;font-size:14px;line-height:26px;color:var(--muted)}

/* firepit */
.thumb{left:111px;width:111px;height:96px;background:#fff;box-shadow:0 2px 6px rgba(0,0,0,.2);display:flex;align-items:center;justify-content:center}
.thumb .ph{width:70px;height:60px;background:radial-gradient(ellipse,#3a3a3a 0%,#777 50%,#fff 72%)}
.fp-photo{left:250px;top:1300px;width:310px;height:320px;background:radial-gradient(ellipse at 50% 45%,rgba(40,40,42,.45) 0%,rgba(60,60,60,.15) 45%,rgba(60,60,60,0) 70%)}
.fp-title{left:617px;top:1286px;font-family:'Montserrat',sans-serif;font-size:38px;line-height:40px;color:var(--navy);font-weight:500}
.fp-title b{font-weight:700}
.fp-text{left:619px;top:1380px;width:470px;font-size:14px;line-height:28px;color:var(--muted);text-align:justify}

/* products */
.section-title{left:0;width:1200px;text-align:center;font-family:'Montserrat',sans-serif;font-size:40px;color:var(--navy);font-weight:500}
.section-title b{font-weight:700}
.card{top:1871px;width:236px;height:359px;background:#fff;border:1px solid var(--line)}
.card.raised{box-shadow:0 4px 14px rgba(0,0,0,.18);border-color:transparent}
.card .img{position:absolute;left:50px;top:18px;width:136px;height:138px;background:radial-gradient(ellipse at 50% 40%,#2f2f31 0%,#6d6e70 38%,#d8d9db 60%,#fff 72%)}
.card .name{position:absolute;left:0;top:166px;width:100%;text-align:center;font-size:17px;line-height:24px;color:#222}
.card .size{position:absolute;left:0;top:226px;width:100%;text-align:center;font-size:12px;color:var(--muted)}
.card .price{position:absolute;left:0;top:256px;width:100%;text-align:center;font-size:22px;font-weight:700;color:var(--red)}
.card .btn{position:absolute;left:51px;top:298px;width:134px;height:40px;font-size:14px;font-weight:500}
.badge-off{position:absolute;left:4px;top:6px;width:40px;height:36px;background:var(--red);color:#fff;font-size:11px;font-weight:700;line-height:12px;text-align:center;padding-top:6px}
.ribbon{position:absolute;right:0;top:12px;width:96px;height:26px;background:var(--navy);color:#fff;font-size:12px;display:flex;align-items:center;justify-content:center;clip-path:polygon(12px 0,100% 0,100% 100%,0 100%)}
.side-tools{position:absolute;left:4px;top:4px;width:38px;height:76px;background:var(--navy)}

/* news */
.news-sub{left:0;top:2566px;width:1200px;text-align:center;font-size:14px;color:#555}
.news-img{top:2611px;width:312px;height:216px}
.news-body{top:2812px;width:290px;height:205px;background:#fff}
.date-tag{position:absolute;left:10px;top:6px;padding:3px 6px;background:var(--navy);color:#fff;font-size:9px}
.news-title{position:absolute;left:20px;top:44px;width:260px;font-size:16px;font-weight:700;line-height:22px;color:#222}
.news-text{position:absolute;left:20px;top:92px;width:262px;font-size:12px;line-height:21px;color:var(--muted)}
.news-body .btn{position:absolute;left:20px;top:157px;width:134px;height:40px;font-size:14px;font-weight:500}

/* footer */
.footer-brand{left:400px;top:3254px;width:400px;text-align:center;color:#fff;font-size:30px;font-weight:500;letter-spacing:1px}
.nl-title{left:111px;top:3346px;color:#fff;font-size:27px;font-weight:400}
.field{background:#fff;border-radius:24px;color:#333;font-size:14px;display:flex;align-items:center;padding-left:34px}
.subscribe{left:937px;top:3339px;width:152px;height:47px;border-radius:24px;background:var(--navy);color:#fff;font-size:16px;font-weight:500;display:flex;align-items:center;justify-content:center}
.rule{height:1px;background:#2e2f36}
.col-head{top:3461px;color:#fff;font-size:16px;font-weight:700}
.links{left:99px;top:3495px;list-style:none;color:#fff;font-size:14px}
.links li{height:28.5px;display:flex;align-items:center;gap:10px}
.info-icon{width:36px;height:36px;border:2px solid #fff;border-radius:50%;display:flex;align-items:center;justify-content:center}
.info-text{color:#fff;font-size:12px;line-height:19px;white-space:nowrap}
.form-box{background:#fff;border:1px solid #ccc;font-size:11px;color:#777;padding:7px 10px}
.submit{left:1049px;top:3684px;width:84px;height:30px;background:var(--navy);color:#fff;font-size:12px;font-weight:700;border-radius:4px;display:flex;align-items:center;justify-content:center}
.copy{left:110px;top:3761px;color:#fff;font-size:12px}
.social{top:3753px;width:32px;height:32px;border:2px solid #fff;border-radius:50%}
</style>
</head>
<body>
<div class="page">

  <div class="abs hero-photo" role="img" aria-label="Charcoal kettle grill with open flames standing on a green lawn"></div>
  <div class="abs hero-grill"></div>

  <svg class="abs" style="left:0;top:0" width="1200" height="3812" viewBox="0 0 1200 3812" aria-hidden="true">
    <defs>
      <linearGradient id="fpPhoto" x1="0" y1="0" x2="1" y2="1">
        <stop offset="0" stop-color="#8a8f7e"/>
        <stop offset=".5" stop-color="#b0a898"/>
        <stop offset="1" stop-color="#c9b9a2"/>
      </linearGradient>
    </defs>
    <polygon points="0,712 429,626 600,789 770,630 1200,650 1200,830 0,830" fill="#fff"/>
    <polyline points="330,646 429,626 600,789 770,630 870,634" fill="none" stroke="var(--navy)" stroke-width="8"/>
    <polygon points="0,1265 600,1173 600,1702 0,1643" fill="url(#fpPhoto)"/>
    <polygon points="600,1173 1200,1265 1200,1643 600,1702" fill="var(--gray-band)"/>
    <polyline points="0,1265 600,1173 1200,1265" fill="none" stroke="var(--navy)" stroke-width="5"/>
    <polyline points="0,1643 600,1702 1200,1643" fill="none" stroke="var(--navy)" stroke-width="5"/>
    <polygon points="0,3172 429,3264 600,3095 770,3264 1200,3172 1200,3812 0,3812" fill="var(--footer)"/>
    <polyline points="0,3172 429,3264 600,3095 770,3264 1200,3172" fill="none" stroke="var(--navy)" stroke-width="8"/>
  </svg>
  <div class="abs fp-photo" role="img" aria-label="Mesh-domed steel firepit on four legs over a stone patio fire ring"></div>

  <div class="abs topbar">
    <span style="left:114px">&#9679; Store location</span>
    <span class="sep" style="left:233px"></span>
    <span style="left:268px">My Cart 0.00</span>
    <span class="sep" style="left:398px"></span>
    <span style="left:431px">Login/Register</span>
    <span style="left:731px">Hotline : +1 555 014 2290</span>
    <span class="sep" style="left:929px"></span>
    <span style="left:953px">English &#9662;</span>
    <span class="sep" style="left:1030px"></span>
    <span style="left:1051px">USD &#9662;</span>
  </div>
  <nav class="abs navbar">
    <a class="active" style="left:114px">Home</a>
    <a style="left:195px">About us</a>
    <a style="left:296px">Product</a>
    <a style="left:385px;font-size:13px">Manufacuring</a>
    <a style="left:755px;font-size:13px">News</a>
    <a style="left:824px;font-size:13px">Reviews</a>
    <a style="left:909px;font-size:13px">Sales &amp;Deals</a>
    <a style="left:1023px;font-size:13px">Contact us</a>
  </nav>
  <svg class="abs brand-diamond" viewBox="0 0 206 206" aria-hidden="true"><polygon points="103,0 206,103 103,206 0,103" fill="var(--navy)"/></svg>
  <div class="abs brand-name">LARKFORGE</div>

  <div class="abs hero-arrow" style="left:73px;top:351px"><svg width="14" height="14" viewBox="0 0 14 14"><polyline points="9,2 4,7 9,12" fill="none" stroke="#fff" stroke-width="2"/></svg></div>
  <div class="abs hero-arrow" style="left:1079px;top:351px"><svg width="14" height="14" viewBox="0 0 14 14"><polyline points="5,2 10,7 5,12" fill="none" stroke="#fff" stroke-width="2"/></svg></div>
  <h1 class="abs hero-title">Larkforge</h1>
  <p class="abs hero-sub">We are an outdoor firepit cookery manufacturer</p>
  <div class="abs btn-outline-light">SHOP NOW</div>

  <h2 class="abs welcome-top">WELCOME</h2>
  <h2 class="abs welcome-brand"><b>LARK</b>FORGE</h2>
  <p class="abs welcome-text">Sed ut perspiciatis unde omnis iste natus error sit voluptatem accusantium doloremque laudantium, totam rem aperiam, eaque ipsa quae ab illo inventore veritatis et quasi architecto beatae vitae dicta sunt explicabo. Nemo enim ipsam voluptatem quia voluptas sit aspernatur aut odit aut fugit, sed quia consequuntur magni dolores</p>
  <div class="abs btn" style="left:518px;top:1037px;width:163px;height:48px">LEARN MORE &raquo;</div>

  <div class="abs thumb" style="top:1283px"><div class="ph" role="img" aria-label="Bowl firepit"></div></div>
  <div class="abs thumb" style="top:1407px"><div class="ph" role="img" aria-label="Domed firepit"></div></div>
  <div class="abs thumb" style="top:1532px"><div class="ph" role="img" aria-label="Folding firepit stand"></div></div>
  <h2 class="abs fp-title"><b>FIREPIT COOKERY</b><br>MANUFACTURER</h2>
  <p class="abs fp-text">Sed ut perspiciatis unde omnis iste natus error sit voluptatem accusantium doloremque laudantium, totam rem aperiam, eaque ipsa quae ab illo inventore veritatis et quasi architecto beatae vitae dicta sunt explicabo. Nemo enim ipsam voluptatem quia voluptas sit aspernatur aut odit aut fugit, sed quia consequuntur magni dolores</p>
  <div class="abs btn" style="left:620px;top:1541px;width:161px;height:46px">LEARN MORE &raquo;</div>

  <h2 class="abs section-title" style="top:1782px"><b>FEATURED</b> PRODUCT</h2>

  <div class="abs card" style="left:111px">
    <div class="img" role="img" aria-label="Bowl firepit on folding stand"></div>
    <div class="badge-off">15%<br>off</div>
    <div class="name">Perspiciatis unde omnis<br>iste natus error</div>
    <div class="size">Size : DNA0054</div>
    <div class="price">$150.25</div>
    <div class="btn">More Details</div>
  </div>
  <div class="abs card raised" style="left:358px">
    <div class="img" role="img" aria-label="Domed mesh firepit on legs"></div>
    <div class="side-tools">
      <svg class="abs" style="left:12px;top:9px" width="14" height="14" viewBox="0 0 14 14"><path d="M1 2h2l2 7h7l1-5H4" fill="none" stroke="#fff" stroke-width="1.5"/><circle cx="6" cy="12" r="1.2" fill="#fff"/><circle cx="11" cy="12" r="1.2" fill="#fff"/></svg>
      <svg class="abs" style="left:12px;top:50px" width="14" height="13" viewBox="0 0 14 13"><path d="M7 12 1.5 6.5A3 3 0 0 1 7 2.5a3 3 0 0 1 5.5 4Z" fill="#fff"/></svg>
    </div>
    <div class="ribbon">Featured</div>
    <div class="name">Perspiciatis unde omnis<br>iste natus error</div>
    <div class="size">Size : DNA0054</div>
    <div class="price">$150.25</div>
    <div class="btn filled">More Details</div>
  </div>
  <div class="abs card" style="left:605px">
    <div class="img" role="img" aria-label="Covered round firepit with curved legs"></div>
    <div class="name">Perspiciatis unde omnis<br>iste natus error</div>
    <div class="size">Size : DNA0054</div>
    <div class="price">$150.25</div>
    <div class="btn">More Details</div>
  </div>
  <div class="abs card" style="left:852px">
    <div class="img" role="img" aria-label="Kettle grill with open flames"></div>
    <div class="badge-off">15%<br>off</div>
    <div class="ribbon">Featured</div>
    <div class="name">Perspiciatis unde omnis<br>iste natus error</div>
    <div class="size">Size : DNA0054</div>
    <div class="price">$150.25</div>
    <div class="btn">More Details</div>
  </div>
  <div class="abs btn" style="left:496px;top:2281px;width:207px;height:53px;font-size:14px;font-weight:500">View more Products</div>

  <div class="abs rule" style="left:111px;top:2420px;width:978px;background:var(--line)"></div>

  <h2 class="abs section-title" style="top:2494px"><b>NEWS FROM</b> LARKFORGE</h2>
  <p class="abs news-sub">Lorem ipsum dolor sit amet, consectetur adipiscing elit, sed do eiusmod tempor incididunt</p>

  <div class="abs news-img" style="left:111px;background:linear-gradient(160deg,#7f9b6a,#4f6b3e 55%,#2f3a2a)" role="img" aria-label="Friends gathered around a garden grill at dusk"></div>
  <div class="abs news-img" style="left:444px;background:linear-gradient(160deg,#5d8a3e,#c7783a 50%,#3a2a22)" role="img" aria-label="Sausages cooking on a barbecue grate"></div>
  <div class="abs news-img" style="left:775px;background:linear-gradient(160deg,#8bab6a,#6a5a48 55%,#2e2a26)" role="img" aria-label="Meat being turned on a smoking grill outdoors"></div>

  <div class="abs news-body" style="left:124px"><span class="date-tag">&#9635; JAN 10,2020</span><div class="news-title">Sed ut perspiciatis unde omnis iste natus error sit</div><div class="news-text">Sed ut perspiciatis unde omnis iste natus error sit voluptatem acusa ntiu m dolorem que lauda</div><div class="btn">More Details</div></div>
  <div class="abs news-body" style="left:456px"><span class="date-tag">&#9635; JAN 10,2020</span><div class="news-title">Sed ut perspiciatis unde omnis iste natus error sit</div><div class="news-text">Sed ut perspiciatis unde omnis iste natus error sit voluptatem acusa ntiu m dolorem que lauda</div><div class="btn">More Details</div></div>
  <div class="abs news-body" style="left:788px"><span class="date-tag">&#9635; JAN 10,2020</span><div class="news-title">Sed ut perspiciatis unde omnis iste natus error sit</div><div class="news-text">Sed ut perspiciatis unde omnis iste natus error sit voluptatem acusa ntiu m dolorem que lauda</div><div class="btn">More Details</div></div>

  <div class="abs footer-brand">LARKFORGE</div>
  <h3 class="abs nl-title">Sign Up Newsletter</h3>
  <div class="abs field" style="left:419px;top:3339px;width:246px;height:47px">Enter Name</div>
  <div class="abs field" style="left:678px;top:3339px;width:247px;height:47px">Enter Email</div>
  <div class="abs subscribe">SUBSCRIBE</div>
  <div class="abs rule" style="left:97px;top:3423px;width:1003px"></div>

  <div class="abs col-head" style="left:99px">Useful Links</div>
  <ul class="abs links">
    <li>&raquo; Home</li><li>&raquo; About us</li><li>&raquo; Product</li><li>&raquo; Manufacuring</li><li>&raquo; News</li><li>&raquo; Reviews</li><li>&raquo; Contact us</li>
  </ul>

  <div class="abs col-head" style="left:304px">Contact Information</div>
  <div class="abs info-icon" style="left:304px;top:3520px"><svg width="14" height="16" viewBox="0 0 14 16"><path d="M7 15S2 9 2 6a5 5 0 0 1 10 0c0 3-5 9-5 9Z" fill="none" stroke="#fff" stroke-width="1.6"/><circle cx="7" cy="6" r="1.8" fill="#fff"/></svg></div>
  <div class="abs info-text" style="left:360px;top:3518px">Lorem ipsum dolor sit amet,<br>consectetur adipiscing elit, sed do</div>
  <div class="abs info-icon" style="left:304px;top:3579px"><svg width="14" height="14" viewBox="0 0 14 14"><path d="M3 1l3 3-2 2a8 8 0 0 0 4 4l2-2 3 3-2 2C6 13 1 8 1 3Z" fill="#fff"/></svg></div>
  <div class="abs info-text" style="left:360px;top:3588px">Phone : +1 555 014 2290</div>
  <div class="abs info-icon" style="left:304px;top:3623px"><svg width="14" height="11" viewBox="0 0 14 11"><rect x="0.5" y="0.5" width="13" height="10" rx="1" fill="#fff"/><polyline points="1,1 7,6 13,1" fill="none" stroke="var(--footer)" stroke-width="1.4"/></svg></div>
  <div class="abs info-text" style="left:360px;top:3632px">Email : info@larkforge.com</div>
  <div class="abs info-icon" style="left:304px;top:3676px"><svg width="14" height="14" viewBox="0 0 14 14"><rect x="1" y="5" width="12" height="8" rx="1" fill="#fff"/><rect x="3.5" y="1" width="7" height="4" fill="none" stroke="#fff" stroke-width="1.4"/></svg></div>
  <div class="abs info-text" style="left:360px;top:3685px">Fax: 0661-55017</div>

  <div class="abs col-head" style="left:638px">Get In Touch:</div>
  <div class="abs form-box" style="left:641px;top:3505px;width:240px;height:31px">Name :</div>
  <div class="abs form-box" style="left:891px;top:3505px;width:240px;height:31px">Phone :</div>
  <div class="abs form-box" style="left:641px;top:3548px;width:490px;height:31px">Email :</div>
  <div class="abs form-box" style="left:641px;top:3590px;width:490px;height:71px">Message :</div>
  <div class="abs submit">SUBMIT</div>

  <div class="abs rule" style="left:97px;top:3735px;width:1003px"></div>
  <div class="abs copy">Copyrights &copy; 2020, Larkforge. All Rights Reserved. &nbsp;| &nbsp;Privacy policy</div>
  <div class="abs social" style="left:983px" aria-label="Social profile"></div>
  <div class="abs social" style="left:1020px" aria-label="Social profile"></div>
  <div class="abs social" style="left:1057px" aria-label="Social profile"></div>

</div>
</body>
</html>
```